Web Design Project

We are an online tax Continuing education provider. We provide online courses for tax preparers. We want the front end page to be user friendly and for the buyer to know exactly what they are looking at. We want a front end page to look smiliar www.larkvalefiling.com. It should have a similar feel to this one.
Our website address will be www.7782QX.com
We currently have another website that is www.LedgrUMs.com but we do not want it to look like this. We want a different look but same information.
We have a logo already which is attached. We don't have specific colors in mind for the front page but don't want it to be too busy looking. It should stand out but not too simple either.
Target Market(s)
Tax Preparers. More serious and professional but these folks are usually not tech savy. Simple, easy to use, and functional is key.
Industry/Entity Type
Education
Requirements
Must have
- Use standard HTML & CSS. NO other coding is needed.
We are looking for 5-7 pages including Home page, log in, FAQ.
Please look at our current website www.LedgrUMs.com and also www.larkvalefiling.com

```html
<!DOCTYPE html>
<html lang="en">
<head>
<meta charset="utf-8">
<title>7782QX – Checkout Details</title>
<link href="https://fonts.googleapis.com/css2?family=PT+Sans:wght@400;700&family=Oswald:wght@300;400;600&display=swap" rel="stylesheet">
<style>
  :root{
    --teal:#24607a;
    --ink:#2b2b2b;
    --muted:#5f5f5f;
    --blue:#6fa1d3;
    --blue-text:#5a97cf;
    --orange-top:#fbc65c;
    --orange-bot:#f7ae3e;
    --gold:#f5b400;
    --red:#e2452a;
    --grey-band:#d9d9d9;
    --page:#e9e9e9;
    --white:#ffffff;
  }
  *{margin:0;padding:0;box-sizing:border-box}
  html,body{width:1024px;height:1200px;overflow:hidden}
  body{position:relative;background:var(--page);font-family:"PT Sans",sans-serif;color:var(--ink)}
  .abs{position:absolute}

  .site-header{left:0;top:0;width:1024px;height:122px;background:var(--white);z-index:2}
  .brand{left:132px;top:60px;display:flex;align-items:center;gap:8px;font-family:"PT Sans",sans-serif;font-weight:700;font-size:30px;color:var(--teal)}
  .brand-dot{width:22px;height:22px;border-radius:50%;background:var(--teal)}
  .nav{top:86px;font-size:12px;color:#111}
  .sign-in{left:817px;top:79px;width:79px;height:26px;border-radius:4px;background:#dfe3e8;border:1px solid #cfd4da;color:#285d95;font-size:12px;display:flex;align-items:center;justify-content:center;gap:7px}

  .hero{left:0;top:122px;width:1024px;height:268px;background:linear-gradient(#d6d6d6,#e6e6e6 40%,#d2d2d2)}
  .hero-base{left:0;top:390px;width:1024px;height:50px;background:linear-gradient(#8f8f8f,#a9a9a9)}
  .hero-title{left:128px;font-family:"Oswald",sans-serif;color:var(--teal);letter-spacing:.2px}
  .hero-dots{left:128px;top:347px;display:flex;gap:6px}
  .hero-dots span{width:10px;height:10px;border-radius:50%;background:#bbb;box-shadow:inset 0 1px 2px #777}
  .hero-dots span.on{background:#fff;box-shadow:none}
  .photo-frame{left:433px;top:166px;width:463px;height:251px;background:var(--white);box-shadow:0 4px 10px rgba(0,0,0,.35);padding:5px}
  .photo{width:100%;height:100%;background:linear-gradient(90deg,#c9a07c 0%,#e39a4a 55%,#c97a35 100%)}

  .features{left:0;top:440px;width:1024px;height:153px;background:var(--grey-band)}
  .feature{top:457px;height:116px;background:linear-gradient(var(--orange-top),var(--orange-bot));padding:14px}
  .feature h3{font-weight:400;font-size:14px;line-height:24px;color:var(--white);letter-spacing:.3px}
  .feature p{font-size:10px;line-height:17px;color:#3a2a10}
  .feature .icon{position:absolute}

  .section-head{left:0;top:593px;width:1024px;height:65px;background:linear-gradient(#dedede,#e7e7e7);border-bottom:1px solid #d2d2d2}
  .section-head h2{position:absolute;left:128px;top:21px;font-weight:400;font-size:16px;color:var(--teal)}

  .intro{left:128px;top:697px;font-size:11.5px;color:#444}

  .cart{left:128px;top:732px;width:600px;height:376px;background:#f3f3f3;border-radius:4px;box-shadow:0 1px 3px rgba(0,0,0,.2);overflow:hidden}
  .cart-head{height:42px;background:linear-gradient(#78a9da,#6a9bcc);color:var(--white);font-size:12px;position:relative}
  .cart-head span{position:absolute;top:14px}
  .cart-row{position:relative;border-bottom:1px solid #d8d8d8}
  .cart-row .check{position:absolute;left:13px;width:9px;height:9px;border:1px solid #888;background:#fff}
  .cart-row .item{position:absolute;left:38px;font-size:10px;line-height:19px;color:#555}
  .cart-row .cost{position:absolute;left:327px;font-size:14px;font-weight:700;color:#666}
  .del{position:absolute}
  .total-label{position:absolute;right:302px;font-size:13px;color:var(--blue-text);text-align:right;white-space:nowrap}
  .total-value{position:absolute;left:327px;font-size:14px;font-weight:700;color:#666}
  .coupon-input{position:absolute;left:329px;top:266px;width:111px;height:33px;background:#fff;border:1px solid #cfcfcf}
  .coupon-btn{position:absolute;left:454px;top:268px;width:106px;height:27px;border-radius:4px;background:linear-gradient(#86b4e0,#6b9dcf);color:#fff;font-size:11.5px;display:flex;align-items:center;justify-content:center}
  .checkout-btn{position:absolute;left:330px;top:324px;width:230px;height:27px;border-radius:4px;background:linear-gradient(#5aa3d4,#1f5f8f);border:1px solid #1c4f78;color:#fff;font-size:11.5px;font-weight:700;letter-spacing:.3px;display:flex;align-items:center;justify-content:center}
  .remove-note{position:absolute;left:46px;top:332px;font-size:11.5px;color:#555;word-spacing:3px}

  .site-footer{left:0;top:1156px;width:1024px;height:44px;background:linear-gradient(#9c9c9c,#b2b2b2);color:var(--white);font-size:10px}
  .site-footer .abs{top:17px}
  .social{display:flex;gap:7px;top:13px!important}
  .social span{width:17px;height:17px;border-radius:50%;background:#e8e8e8}
</style>
</head>
<body>

<header class="site-header abs">
  <div class="brand abs"><span class="brand-dot"></span>7782QX</div>
  <span class="nav abs" style="left:490px">Home</span>
  <span class="nav abs" style="left:571px">Courses</span>
  <span class="nav abs" style="left:663px">FAQ</span>
  <span class="nav abs" style="left:736px">Contact</span>
  <div class="sign-in abs">
    <svg width="8" height="10" viewBox="0 0 8 10"><circle cx="4" cy="2.5" r="2.2" fill="#285d95"/><path d="M0 10 Q0 5 4 5 Q8 5 8 10Z" fill="#285d95"/></svg>
    Sign In
  </div>
</header>

<section class="hero abs"></section>
<div class="hero-base abs"></div>
<h1 class="hero-title abs" style="top:172px;font-size:21px;font-weight:600">EASY-TO-UNDERSTAND,</h1>
<p class="hero-title abs" style="top:212px;font-size:20px;font-weight:300">AFFORDABLE CONTINUING EDUCATION</p>
<p class="hero-title abs" style="top:250px;font-size:20px;font-weight:300">AT YOUR FINGER TIPS</p>
<div class="hero-dots abs"><span></span><span></span><span></span><span class="on"></span></div>
<div class="photo-frame abs">
  <div class="photo" role="img" aria-label="Photo of a student studying on a laptop in a lecture hall"></div>
</div>

<section class="features abs"></section>
<article class="feature abs" style="left:128px;width:250px">
  <h3>IRS APPROVED<br>PROVIDER</h3>
  <p style="margin-top:8px">Click here to see our<br>approved provider link at IRS website</p>
  <svg class="icon" style="left:172px;top:16px" width="60" height="52" viewBox="0 0 60 52"><circle cx="30" cy="26" r="24" fill="#fff" opacity=".9"/></svg>
</article>
<article class="feature abs" style="left:386px;width:251px">
  <h3>CERTIFICATE OF<br>COMPLETION</h3>
  <p style="margin-top:8px">IMPORTANT! All federal tax return&nbsp; preparers<br>must have a current year PTIN.</p>
  <svg class="icon" style="left:184px;top:19px" width="50" height="42" viewBox="0 0 50 42"><rect x="1" y="1" width="47" height="38" fill="#f4f4f4" stroke="#8a8a8a"/><rect x="5" y="5" width="39" height="30" fill="none" stroke="#c9c9c9"/><line x1="12" y1="15" x2="36" y2="15" stroke="#999"/><line x1="12" y1="21" x2="32" y2="21" stroke="#999"/><circle cx="36" cy="29" r="4" fill="#e5b53a"/></svg>
</article>
<article class="feature abs" style="left:645px;width:251px">
  <h3 style="padding-left:2px">PROFESSIONAL</h3>
  <p style="margin-top:15px;margin-left:-2px">Complete your continuing education<br>requirements now so you can concentrate<br>on servicing your tax clients.</p>
  <div class="icon" style="left:186px;top:12px;width:54px;height:54px;border-radius:4px;background:linear-gradient(135deg,#e6d7b5,#c9903c)" role="img" aria-label="Drafting tools illustration"></div>
</article>

<section class="section-head abs"><h2>Checkout Details</h2></section>

<p class="intro abs">Select your Package(s) in the desired format and add to cart.</p>

<section class="cart abs">
  <div class="cart-head">
    <span style="left:38px">Item</span>
    <span style="left:328px">Cost</span>
    <span style="left:477px">Delete</span>
  </div>
  <div class="cart-row" style="height:55px">
    <span class="check" style="top:21px"></span>
    <p class="item" style="top:8px">15 Hour Package for IRS Registered<br>Tax Preparer CE</p>
    <span class="cost" style="top:16px">$42.00</span>
    <svg class="del" style="left:478px;top:19px" width="12" height="12" viewBox="0 0 12 12"><path d="M1 1L11 11M11 1L1 11" stroke="var(--red)" stroke-width="2.6" stroke-linecap="round"/></svg>
  </div>
  <div class="cart-row" style="height:58px">
    <svg class="check" style="top:11px;border-color:#5a7fb0" viewBox="0 0 9 9"><path d="M1.5 4.5L3.8 7L8 1" stroke="#2a5fa5" stroke-width="1.6" fill="none"/></svg>
    <p class="item" style="top:10px;left:39px">15 Hour Package for IRS Registered<br>Tax Preparer CE</p>
    <span class="cost" style="top:20px">$99.90</span>
    <svg class="del" style="left:478px;top:24px" width="12" height="12" viewBox="0 0 12 12"><path d="M1 1L11 11M11 1L1 11" stroke="var(--red)" stroke-width="2.6" stroke-linecap="round"/></svg>
  </div>

  <span class="total-label" style="top:168px">Sub Total :</span>
  <span class="total-value" style="top:167px">$0.00</span>
  <span class="total-label" style="top:200px">Discount :</span>
  <span class="total-value" style="top:199px">$0.00</span>
  <span class="total-label" style="top:234px">Total Cost :</span>
  <span class="total-value" style="top:227px;font-size:20px;color:var(--gold)">141.90</span>
  <span class="total-label" style="top:264px">Enter Discount code: (if applicable) :</span>
  <div class="coupon-input"></div>
  <div class="coupon-btn">Apply Coupon</div>

  <svg class="del" style="left:18px;top:332px" width="12" height="12" viewBox="0 0 12 12"><path d="M1 1L11 11M11 1L1 11" stroke="var(--red)" stroke-width="2.6" stroke-linecap="round"/></svg>
  <p class="remove-note">Click to remove the item from your cart.</p>
  <div class="checkout-btn">PROCEED TO CHECKOUT</div>
</section>

<footer class="site-footer abs">
  <span class="abs" style="left:128px">Copyright © 2012. All Rights Reserved</span>
  <span class="abs" style="left:426px;font-size:9.5px;color:#eef">Terms &amp; Condition &nbsp;&nbsp;|&nbsp;&nbsp; Privacy Policy</span>
  <span class="abs" style="left:756px;font-size:9.5px">Social Media</span>
  <div class="social abs" style="left:830px"><span></span><span></span><span></span></div>
</footer>

</body>
</html>
```